Website re-design for Brightmoor LLC website ( has existing website )

Looking to do a complete re-design of Brightmoorllc. The existing website is dated and built in wordpress. The new website will not be wordpress. The project folder includes an overview.txt file with details on the project. The file also contains a list of websites that he/she likes which I am sure is very helpful .
Number of Pages Required
1 page

```html
<!DOCTYPE html>
<html lang="en">
<head>
<meta charset="utf-8">
<title>Brightmoor LLC</title>
<link rel="stylesheet" href="https://fonts.googleapis.com/css2?family=Poppins:wght@400;500;600;700&family=Roboto:ital,wght@0,400;0,500;0,700;1,400&display=swap">
<style>
:root{
  --blue:#0b6dbf;
  --blue-dark:#0a5fa8;
  --blue-light:#1d83d4;
  --ink:#1e1e1e;
  --muted:#7a7a7a;
  --pale:#e9f1f9;
  --grey-bg:#f4f4f4;
  --footer:#121212;
  --white:#ffffff;
}
*{margin:0;padding:0;box-sizing:border-box}
html,body{width:1200px;height:4183px;overflow:hidden;background:var(--white)}
body{font-family:'Roboto',sans-serif;color:var(--ink)}
.page{position:relative;width:1200px;height:4183px;overflow:hidden}
.abs{position:absolute}
.heading{font-family:'Poppins',sans-serif;font-weight:500;font-size:40px;text-align:center;width:100%;color:var(--ink)}
.heading .accent{color:var(--blue)}
.divider{position:absolute;left:530px;width:140px;height:14px}
.btn{position:absolute;display:flex;align-items:center;justify-content:center;gap:8px;border-radius:24px;font-family:'Roboto',sans-serif;font-weight:700;font-size:16px;text-transform:uppercase;letter-spacing:.2px}
.btn-blue{background:var(--blue);color:var(--white)}
.btn-white{background:var(--white);color:var(--blue)}
.btn .dot{width:15px;height:15px;border-radius:50%;display:inline-flex;align-items:center;justify-content:center}
.btn-blue .dot{background:var(--white)}
.btn-white .dot{background:var(--blue)}

/* header */
.logo{display:flex;align-items:center;gap:10px}
.logo .mark{width:62px;height:62px;border-radius:50%;background:var(--blue)}
.logo .name{font-family:'Poppins',sans-serif;font-weight:400;font-size:32px;color:var(--blue);letter-spacing:-.5px}
.nav{position:absolute;top:72px;left:429px;display:flex;gap:21px;font-size:14.5px;color:var(--ink)}
.nav .active{color:var(--blue);position:relative}
.nav .active::before{content:"";position:absolute;top:-9px;left:50%;width:7px;height:7px;margin-left:-3.5px;border-radius:50%;background:var(--blue)}
.callbox{position:absolute;left:718px;top:14px;display:flex;gap:12px;align-items:center}
.callbox .ico{width:34px;height:34px;border-radius:50%;background:var(--blue);display:flex;align-items:center;justify-content:center}
.callbox small{display:block;font-size:10.5px;font-weight:500;color:var(--ink)}
.callbox b{display:block;font-size:19px;font-weight:500;color:var(--blue)}
.estimate{left:937px;top:16px;width:150px;height:40px;font-size:15px;text-transform:none;font-weight:500}

/* hero */
.hero-title{top:312px;width:100%;text-align:center;font-family:'Poppins',sans-serif;font-weight:600;font-size:37px;color:var(--white)}
.hero-text{top:378px;left:330px;width:540px;text-align:center;font-size:16.5px;line-height:27px;color:var(--white)}
.hero-arrow{width:40px;height:40px;border-radius:50%;background:rgba(0,0,0,.75);display:flex;align-items:center;justify-content:center}

/* services */
.card{position:absolute;width:307px;height:352px;background:var(--white);box-shadow:0 2px 12px rgba(0,0,0,.1);text-align:center}
.card .photo{position:absolute;left:10px;top:10px;width:287px;height:211px}
.card h3{position:absolute;top:247px;width:100%;font-size:16.5px;font-weight:500;color:var(--ink)}
.card p{position:absolute;top:278px;left:18px;right:18px;font-size:13.5px;line-height:24px;color:var(--muted)}
.card.featured{background:var(--blue);height:367px;box-shadow:none}
.card.featured h3{top:239px;color:var(--white)}
.card.featured p{top:270px;color:var(--white)}
.card .more{position:absolute;left:132px;bottom:-24px;width:44px;height:44px;border-radius:50%;background:var(--blue);border:2px solid var(--white);display:flex;align-items:center;justify-content:center}

/* about */
.about-title{left:593px;top:2022px;font-family:'Poppins',sans-serif;font-weight:600;font-size:38px;line-height:48px;color:var(--white)}
.about-rule{left:593px;top:2130px;width:66px;height:3px;background:var(--white)}
.about-copy{left:593px;top:2163px;width:497px;font-size:13.6px;line-height:26.8px;color:var(--white);text-align:justify}
.about-copy p+p{margin-top:12px}

/* gallery */
.shot{position:absolute}
.shot.faded{opacity:.45}
.shot .tag{position:absolute;bottom:12px;width:100%;text-align:center;color:var(--white);font-weight:700;font-size:17px}
.pager{left:508px;top:3025px;display:flex;align-items:center;gap:14px}
.pager .num{font-family:'Poppins',sans-serif;font-weight:600;font-size:20px}
.pager .num small{font-size:13px;font-weight:400;color:var(--muted)}

/* testimonial */
.testimonial{left:0;top:3142px;width:1200px;height:309px;background:var(--pale)}
.avatar{left:161px;top:3227px;width:140px;height:140px;border-radius:50%;border:3px solid var(--blue);padding:6px;background:var(--white)}
.avatar .face{width:100%;height:100%;border-radius:50%;background:linear-gradient(160deg,#d7d1c8,#8e7a69 60%,#3b4a5c)}
.t-title{left:349px;top:3190px;font-family:'Poppins',sans-serif;font-weight:500;font-size:36px}
.t-title .accent{color:var(--blue)}
.quote-mark{font-family:'Poppins',sans-serif;font-weight:700;font-size:64px;color:var(--blue);line-height:1}
.t-quote{left:350px;top:3264px;width:650px;font-style:italic;font-size:13.8px;line-height:25px;color:var(--muted)}
.t-name{left:350px;top:3333px;font-size:16.5px;font-weight:500}
.t-place{left:350px;top:3357px;font-size:12px;color:#a3a3a3}

/* contact */
.contact-left{left:0;top:3451px;width:698px;height:560px;background:var(--grey-bg)}
.contact-right{left:698px;top:3451px;width:502px;height:560px;background:var(--blue)}
.c-title{left:138px;top:3494px;font-family:'Poppins',sans-serif;font-weight:500;font-size:40px}
.c-title .accent{color:var(--blue)}
.c-rule{left:141px;top:3552px;width:54px;height:3px;background:var(--blue)}
.field{position:absolute;background:var(--white);border:1px solid #cfcfcf;font-size:12.5px;color:#555;padding:14px 18px}
.info{position:absolute;left:746px;display:flex;gap:24px;align-items:center;color:var(--white)}
.info .ring{width:50px;height:50px;border-radius:50%;border:2px solid var(--white);display:flex;align-items:center;justify-content:center;flex:none}
.info h4{font-size:20px;font-weight:500;text-transform:uppercase;line-height:24px}
.info p{font-size:14.5px;line-height:20px}

/* footer */
.foot-nav{left:460px;top:4033px;display:flex;gap:20px;font-size:14px;color:var(--white)}
.foot-contact{top:4066px;display:flex;gap:8px;align-items:center;font-size:15.5px;color:var(--white)}
.copyright{left:110px;top:4110px;font-size:14px;color:var(--white)}
.social{width:36px;height:36px;border-radius:50%;border:2px solid var(--white)}
.footer .logo .name{color:var(--blue)}
</style>
</head>
<body>
<div class="page">

  <svg width="0" height="0" class="abs" aria-hidden="true">
    <defs>
      <symbol id="i-phone" viewBox="0 0 24 24"><path fill="currentColor" d="M6.6 10.8a15 15 0 0 0 6.6 6.6l2.2-2.2a1 1 0 0 1 1-.25 11.4 11.4 0 0 0 3.6.57 1 1 0 0 1 1 1V20a1 1 0 0 1-1 1A17 17 0 0 1 3 4a1 1 0 0 1 1-1h3.5a1 1 0 0 1 1 1c0 1.25.2 2.45.57 3.57a1 1 0 0 1-.25 1z"/></symbol>
      <symbol id="i-chev" viewBox="0 0 24 24"><path fill="none" stroke="currentColor" stroke-width="3" stroke-linecap="round" stroke-linejoin="round" d="M9 6l6 6-6 6"/></symbol>
      <symbol id="i-pin" viewBox="0 0 24 24"><path fill="currentColor" d="M12 2a7 7 0 0 0-7 7c0 5 7 13 7 13s7-8 7-13a7 7 0 0 0-7-7zm0 9.5A2.5 2.5 0 1 1 12 6.5a2.5 2.5 0 0 1 0 5z"/></symbol>
      <symbol id="i-fax" viewBox="0 0 24 24"><path fill="currentColor" d="M7 3h8l2 2v4H7zM4 10h16a1 1 0 0 1 1 1v8a1 1 0 0 1-1 1H4a1 1 0 0 1-1-1v-8a1 1 0 0 1 1-1zm3 5v3h10v-3z"/></symbol>
      <symbol id="i-mail" viewBox="0 0 24 24"><path fill="currentColor" d="M3 5h18a1 1 0 0 1 1 1v12a1 1 0 0 1-1 1H3a1 1 0 0 1-1-1V6a1 1 0 0 1 1-1zm9 8 8-5.5V7l-8 5.5L4 7v.5z"/></symbol>
      <symbol id="i-divider" viewBox="0 0 140 14"><line x1="0" y1="7" x2="50" y2="7" stroke="#0b6dbf" stroke-width="2"/><circle cx="70" cy="7" r="7" fill="#0b6dbf"/><line x1="90" y1="7" x2="140" y2="7" stroke="#0b6dbf" stroke-width="2"/></symbol>
    </defs>
  </svg>

  <!-- Header -->
  <header>
    <div class="logo abs" style="left:110px;top:18px">
      <span class="mark"></span><span class="name">Brightmoor</span>
    </div>
    <div class="callbox">
      <span class="ico"><svg width="18" height="18" style="color:#fff"><use href="#i-phone"/></svg></span>
      <div><small>Call Us Today!</small><b>(555) 014-2276</b></div>
    </div>
    <div class="btn btn-blue estimate">Free Estimate</div>
    <nav class="nav">
      <span class="active">Home</span><span>Services</span><span>About Us</span><span>FAQs</span><span style="margin-left:12px">Employment</span><span>Testimonials</span><span>Gallery</span><span>Contact Us</span>
    </nav>
  </header>

  <!-- Hero -->
  <section class="hero">
    <svg class="abs" style="left:0;top:99px" width="1200" height="701" viewBox="0 0 1200 701">
      <defs>
        <linearGradient id="heroGrad" x1="0" y1="0" x2="1" y2="1">
          <stop offset="0" stop-color="#5a4a38"/>
          <stop offset=".45" stop-color="#3d3f35"/>
          <stop offset="1" stop-color="#24323a"/>
        </linearGradient>
      </defs>
      <rect width="1200" height="701" fill="url(#heroGrad)" role="img" aria-label="Divers clearing weeds from the water beside a wooden dock"/>
      <path d="M0,548 Q600,772 1200,532 L1200,701 L0,701Z" fill="#fff"/>
      <path d="M0,568 Q600,800 1200,550" fill="none" stroke="#0b6dbf" stroke-width="9"/>
    </svg>
    <div class="abs hero-arrow" style="left:34px;top:352px"><svg width="18" height="18" style="color:#fff;transform:scaleX(-1)"><use href="#i-chev"/></svg></div>
    <div class="abs hero-arrow" style="left:1125px;top:352px"><svg width="18" height="18" style="color:#fff"><use href="#i-chev"/></svg></div>
    <h1 class="abs hero-title">Reclaim Open Water</h1>
    <p class="abs hero-text">Brightmoor LLC is a company formed in response to the increase in invasive species in Minnesota lakes and waterways.</p>
    <div class="btn btn-blue" style="left:497px;top:453px;width:206px;height:48px">Get Started <span class="dot"><svg width="10" height="10" style="color:#0b6dbf"><use href="#i-chev"/></svg></span></div>
    <svg class="abs" style="left:568px;top:748px" width="64" height="64" viewBox="0 0 64 64">
      <circle cx="32" cy="32" r="30" fill="#fff" stroke="#d6e4f2" stroke-width="2"/>
      <path d="M32 16c-5 5-7 10-7 16s2 11 7 16c5-5 7-10 7-16s-2-11-7-16z" fill="none" stroke="#0b6dbf" stroke-width="2"/>
      <line x1="25" y1="32" x2="39" y2="32" stroke="#0b6dbf" stroke-width="2"/>
    </svg>
  </section>

  <!-- Services -->
  <section class="services">
    <h2 class="abs heading" style="top:856px">Our <span class="accent">Services</span></h2>
    <svg class="divider" style="top:914px"><use href="#i-divider"/></svg>

    <article class="card" style="left:110px;top:976px">
      <div class="photo" role="img" aria-label="Wooden dock running through tall reeds" style="background:linear-gradient(180deg,#4f7a3a,#7f9a5a 45%,#a69a82)"></div>
      <h3>Dock Install and Removal Services</h3>
      <p>Lorem ipsum dolor sit amet, consectetur adipiscing elit, sed do eiusmod</p>
    </article>
    <article class="card featured" style="left:447px;top:968px">
      <div class="photo" role="img" aria-label="Canopy frame over a boat lift on a lake" style="background:linear-gradient(180deg,#4b8fd8,#8bbcef 45%,#1f4d7a 60%,#6d6a63)"></div>
      <h3>Canopy Services</h3>
      <p>Lorem ipsum dolor sit amet, consectetur adipiscing elit, sed do eiusmod</p>
      <span class="more"><svg width="16" height="16" style="color:#fff"><use href="#i-chev"/></svg></span>
    </article>
    <article class="card" style="left:781px;top:976px">
      <div class="photo" role="img" aria-label="Barge on a lake at sunset seen from a dock" style="background:linear-gradient(180deg,#2e4a73,#c98a4a 42%,#3a3a44 60%,#1e1e22)"></div>
      <h3>Barge Services</h3>
      <p>Lorem ipsum dolor sit amet, consectetur adipiscing elit, sed do eiusmod</p>
    </article>

    <article class="card" style="left:110px;top:1389px">
      <div class="photo" role="img" aria-label="Dock lift with canopy frame on a lake" style="background:linear-gradient(180deg,#5a94d6,#a9cdf0 40%,#2b5c8c 62%,#7e8f9a)"></div>
      <h3>Dock Lift Services</h3>
      <p>Lorem ipsum dolor sit amet, consectetur adipiscing elit, sed do eiusmod</p>
    </article>
    <article class="card" style="left:447px;top:1389px">
      <div class="photo" role="img" aria-label="Weed harvesting boat on a trailer" style="background:linear-gradient(180deg,#b9b7b0,#8a8880 45%,#4a3f3a 70%,#8c7e70)"></div>
      <h3>Aquatic Weed Removal</h3>
      <p>Lorem ipsum dolor sit amet, consectetur adipiscing elit, sed do eiusmod</p>
    </article>
    <article class="card" style="left:781px;top:1389px">
      <div class="photo" role="img" aria-label="Volunteers in safety vests collecting litter by a beach" style="background:linear-gradient(180deg,#3f6a3a,#7b9a5e 50%,#c7b48a)"></div>
      <h3>Beach Clean Up Services</h3>
      <p>Lorem ipsum dolor sit amet, consectetur adipiscing elit, sed do eiusmod</p>
    </article>

    <div class="btn btn-blue" style="left:479px;top:1790px;width:241px;height:48px">View All Services <span class="dot"><svg width="10" height="10" style="color:#0b6dbf"><use href="#i-chev"/></svg></span></div>
  </section>

  <!-- About -->
  <section class="about">
    <svg class="abs" style="left:0;top:1900px" width="1200" height="594" viewBox="0 0 1200 594">
      <path d="M0,148 C300,30 800,-8 1200,2 L1200,594 L0,594Z" fill="#1d83d4"/>
      <path d="M0,166 C300,50 800,14 1200,26" fill="none" stroke="#fff" stroke-width="4"/>
      <path d="M0,176 C300,62 800,26 1200,36 L1200,594 L0,594Z" fill="#0b6dbf"/>
    </svg>
    <svg class="abs" style="left:109px;top:2038px" width="400" height="400" viewBox="0 0 400 400">
      <defs>
        <linearGradient id="sunsetGrad" x1="0" y1="0" x2="0" y2="1">
          <stop offset="0" stop-color="#3a6ea6"/>
          <stop offset=".38" stop-color="#e39a52"/>
          <stop offset=".5" stop-color="#2f4d72"/>
          <stop offset="1" stop-color="#1a2a3a"/>
        </linearGradient>
      </defs>
      <circle cx="200" cy="200" r="188" fill="url(#sunsetGrad)" role="img" aria-label="Lake at sunset seen from a wooden dock"/>
      <circle cx="200" cy="200" r="194" fill="none" stroke="#2a86d6" stroke-width="8"/>
    </svg>
    <h2 class="abs about-title">Aquatic Innovators, at<br>Your Service.</h2>
    <div class="abs about-rule"></div>
    <div class="abs about-copy">
      <p>Brightmoor LLC is a company formed in response to the increasing incidence of invasive species in Minnesota's lakes and water systems. The impact of these fast-growing nuisances, inspired our venture to effectively control unwanted lake weeds. Brightmoor, LLC helps provide the enjoyable weed-free lake environment craved by water enthusiasts.</p>
      <p>We have partnered with Green Loop Compost to recycle 100% of the lake weeds we remove.</p>
    </div>
    <div class="btn btn-white" style="left:594px;top:2389px;width:185px;height:45px;font-size:15px">Learn More <span class="dot"><svg width="10" height="10" style="color:#fff"><use href="#i-chev"/></svg></span></div>
  </section>

  <!-- Gallery -->
  <section class="gallery">
    <h2 class="abs heading" style="top:2555px"><span class="accent">Our</span> Gallery</h2>
    <svg class="divider" style="top:2613px"><use href="#i-divider"/></svg>

    <div class="shot faded" role="img" aria-label="Dock lift on a calm lake" style="left:122px;top:2715px;width:94px;height:228px;background:linear-gradient(180deg,#c9d6e2,#8ea4b6)"></div>
    <div class="shot faded" role="img" aria-label="Misty lake view" style="left:216px;top:2684px;width:153px;height:291px;background:linear-gradient(180deg,#cfd6dc,#9aa6ae)"></div>
    <div class="shot" role="img" aria-label="Dock covered in weeds before cleaning" style="left:370px;top:2663px;width:229px;height:333px;background:linear-gradient(180deg,#9fb0b4,#4e6a3a 32%,#5e5a46 70%,#3e3a30)"><span class="tag">Before</span></div>
    <div class="shot" role="img" aria-label="Clean dock after weed removal" style="left:606px;top:2663px;width:229px;height:333px;background:linear-gradient(180deg,#5f7e45,#6c8a4e 35%,#7a7466 70%,#4c463c)"><span class="tag">After</span></div>
    <div class="shot faded" role="img" aria-label="Barge on a lake" style="left:836px;top:2684px;width:148px;height:291px;background:linear-gradient(180deg,#dcd6ce,#a9a296)"></div>
    <div class="shot faded" role="img" aria-label="Water surface" style="left:986px;top:2715px;width:94px;height:228px;background:linear-gradient(180deg,#d3dbe0,#a3b0b8)"></div>

    <div class="abs pager">
      <svg width="40" height="40" viewBox="0 0 40 40"><rect x="8" y="8" width="24" height="24" transform="rotate(45 20 20)" fill="none" stroke="#cfcfcf" stroke-width="2"/><path d="M27 20H13m5-5-5 5 5 5" fill="none" stroke="#cfcfcf" stroke-width="2"/></svg>
      <span class="num">01 <small>/12</small></span>
      <svg width="56" height="56" viewBox="0 0 56 56"><rect x="12" y="12" width="32" height="32" transform="rotate(45 28 28)" fill="none" stroke="#0b6dbf" stroke-width="3"/><path d="M17 28h22m-7-7 7 7-7 7" fill="none" stroke="#0b6dbf" stroke-width="3"/></svg>
    </div>
  </section>

  <!-- Testimonial -->
  <section>
    <div class="abs testimonial"></div>
    <div class="abs avatar"><div class="face" role="img" aria-label="Portrait of the association representative"></div></div>
    <h2 class="abs t-title">What our <span class="accent">clients say</span></h2>
    <span class="abs quote-mark" style="left:305px;top:3240px">&ldquo;</span>
    <p class="abs t-quote">Everyone used to jump off the water trampoline and instantly get tangled in lake weeds. We contacted Brightmoor and their SCUBA divers have now been solving our problem for the past 4 years!</p>
    <span class="abs quote-mark" style="left:935px;top:3295px">&rdquo;</span>
    <p class="abs t-name">Maple Ridge Shores Association</p>
    <p class="abs t-place">Lake Wendell</p>
  </section>

  <!-- Contact -->
  <section class="contact">
    <div class="abs contact-left"></div>
    <div class="abs contact-right"></div>
    <h2 class="abs c-title">Contact <span class="accent">Us</span></h2>
    <div class="abs c-rule"></div>
    <div class="field" style="left:141px;top:3589px;width:236px;height:44px">Name :</div>
    <div class="field" style="left:388px;top:3589px;width:234px;height:44px">Phone :</div>
    <div class="field" style="left:141px;top:3641px;width:481px;height:44px">Email :</div>
    <div class="field" style="left:141px;top:3693px;width:481px;height:97px">Message :</div>
    <div class="btn btn-blue" style="left:141px;top:3805px;width:114px;height:43px;font-size:16px">Submit</div>

    <div class="info" style="top:3546px"><span class="ring"><svg width="20" height="20" style="color:#fff"><use href="#i-pin"/></svg></span><div><h4>Address</h4><p>4180 Birch Lane Northfield, MN 55010</p></div></div>
    <div class="info" style="top:3619px"><span class="ring"><svg width="20" height="20" style="color:#fff"><use href="#i-phone"/></svg></span><div><h4>Phone</h4><p>(555) 014-2276</p></div></div>
    <div class="info" style="top:3692px"><span class="ring"><svg width="20" height="20" style="color:#fff"><use href="#i-fax"/></svg></span><div><h4>Fax</h4><p>+1 555 018 4470</p></div></div>
    <div class="info" style="top:3768px"><span class="ring"><svg width="20" height="20" style="color:#fff"><use href="#i-mail"/></svg></span><div><h4>Email</h4><p>contact@brightmoorllc.com</p></div></div>
  </section>

  <!-- Footer -->
  <footer class="footer">
    <svg class="abs" style="left:0;top:3870px" width="1200" height="313" viewBox="0 0 1200 313">
      <path d="M0,130 Q600,-30 1200,100 L1200,313 L0,313Z" fill="#fff"/>
      <path d="M0,146 Q600,-14 1200,116" fill="none" stroke="#0b6dbf" stroke-width="7"/>
      <path d="M0,158 Q600,2 1200,128 L1200,313 L0,313Z" fill="#121212"/>
    </svg>
    <div class="logo abs" style="left:110px;top:4040px">
      <span class="mark" style="width:52px;height:52px"></span><span class="name" style="font-size:27px">Brightmoor</span>
    </div>
    <nav class="abs foot-nav">
      <span>Home</span><span>Services</span><span>About Us</span><span>FAQs</span><span style="margin-left:10px">Employment</span><span>Testimonials</span><span>Gallery</span><span>Contact Us</span>
    </nav>
    <div class="abs foot-contact" style="left:746px"><svg width="14" height="14" style="color:#fff"><use href="#i-phone"/></svg>(555) 014-2276</div>
    <div class="abs foot-contact" style="left:903px"><svg width="16" height="16" style="color:#fff"><use href="#i-mail"/></svg>info@brightmoorllc.com</div>
    <p class="abs copyright">&copy;2022 brightmoorllc.com All rights reserved.</p>
    <span class="abs social" style="left:1007px;top:4109px"></span>
    <span class="abs social" style="left:1051px;top:4109px"></span>
  </footer>

</div>
</body>
</html>
```